Website for Torvel Capital - investment banking firm

We have a corporate identity (thanks to Ravinka/31842) and want to extend that into a website design.  See the attached zipped files.
We have software folks in-house to do the coding.
See the attached Project Brief & Notes for more details.  Don't worry about the actual text - lorem ipsum will be fine.
The server will be Apache.
Thank you!
Desmond

Industry/Entity Type
Investment

```html
<!DOCTYPE html>
<html lang="en">
<head>
<meta charset="utf-8">
<title>Torvel Capital – Investment Banking</title>
<link href="https://fonts.googleapis.com/css2?family=Open+Sans:wght@300;400;600&family=Raleway:wght@300;600&display=swap" rel="stylesheet">
<style>
:root{
  --bar:#1e1e1e;
  --brand:#0a7ba1;
  --brand-link:#0a6f95;
  --ink:#2a2a2a;
  --muted:#555;
  --band:#e9e9e9;
  --map:#e3e3e3;
  --footer:#232323;
  --footer-deep:#161616;
  --footer-text:#c9c9c9;
  --white:#fff;
}
*{box-sizing:border-box;margin:0;padding:0}
html,body{width:1038px;height:1200px;overflow:hidden;background:var(--white)}
body{font-family:"Open Sans",Arial,sans-serif;color:var(--ink);position:relative}
.abs{position:absolute}
ul{list-style:none}

/* top bar */
.topbar{left:0;top:0;width:1038px;height:42px;background:var(--bar);color:var(--white);font-size:13px}
.topbar .region{left:95px;top:11px;display:flex;align-items:center;gap:8px}
.topbar .sep{margin:0 6px}
.pill{top:10px;height:22px;background:var(--white);color:#222;border-radius:2px;font-size:11px;display:flex;align-items:center;justify-content:center;gap:6px}
.pill.phone{left:761px;width:102px}
.pill.login{left:874px;width:69px}

/* header */
.header{left:0;top:42px;width:1038px;height:95px;background:var(--brand)}
.logo{left:95px;top:28px;display:flex;align-items:center;gap:12px;color:var(--white)}
.logo .square{width:34px;height:34px;background:var(--white)}
.logo .name{font-size:22px;font-weight:400;letter-spacing:.5px}
.nav{right:94px;top:36px;display:flex;align-items:center;gap:0;font-size:11px;color:var(--white);text-transform:uppercase}
.nav li{padding:6px 14px}
.nav li.active{background:var(--bar);padding:6px 15px}

/* hero */
.worldmap{left:86px;top:137px;width:918px;height:311px;background:radial-gradient(ellipse at 50% 45%,#e0e0e0 0%,#e6e6e6 55%,rgba(255,255,255,0) 80%)}
.hero-title{left:0;top:192px;width:1038px;text-align:center;font-family:"Raleway",sans-serif;font-weight:300;font-size:35px;line-height:40px;color:#222}
.hero-title b{font-weight:600}
.hero-text{left:225px;top:300px;width:588px;text-align:center;font-size:11px;line-height:17.5px;font-weight:300;color:#444}
.btn{left:441px;top:371px;width:156px;height:35px;border:1px solid #222;border-radius:3px;background:var(--white);font-size:15px;font-weight:300;display:flex;align-items:center;justify-content:center}

/* services band */
.band{left:0;top:470px;width:1038px;height:204px;background:var(--band)}
.service{top:503px;width:270px}
.service h2{font-weight:400;font-size:17.5px;margin-bottom:12px;color:#222}
.service li{font-size:11px;font-weight:300;color:#333;line-height:24px;padding-left:13px;position:relative}
.service li::before{content:"›";position:absolute;left:0;color:var(--brand)}
.service li.more{line-height:16px;color:var(--brand-link)}
.divider{top:500px;width:1px;height:165px;background:#d6d6d6}

/* positioning */
.position{left:95px;top:708px;width:470px}
.position h2{font-weight:400;font-size:21px;color:#222}
.position h2 small{font-size:11px;font-weight:400}
.position p{font-size:11px;font-weight:300;line-height:15.5px;color:#444}
.position .intro{margin-top:22px}
.position .point{margin-top:14px;padding-left:18px;position:relative}
.position .point::before{content:"→";position:absolute;left:0;top:-1px;color:var(--brand);font-weight:600}
.position .point a{color:var(--brand-link);text-decoration:none}
.dotted{left:588px;top:718px;height:206px;border-left:1px dotted #999}
.location{left:618px;top:708px}
.location h2{font-weight:400;font-size:21px;color:#222}
.mapframe{left:618px;top:754px;width:323px;height:142px;background:var(--white);padding:4px;box-shadow:0 3px 6px rgba(0,0,0,.35)}
.mapframe div{width:100%;height:100%;background:linear-gradient(135deg,#e2ded6,#ece9e2 55%,#ded9cf)}

/* footer */
.footer{left:0;top:982px;width:1038px;height:180px;background:var(--footer);color:var(--footer-text)}
.fcol{top:18px}
.fcol h3{font-weight:400;font-size:15.5px;color:var(--white);margin-bottom:16px}
.fcol li{font-size:10.5px;line-height:17.3px;padding-left:13px;position:relative}
.fcol li::before{content:"•";position:absolute;left:0;font-size:9px}
.fcol.contact li{padding-left:18px}
.fcol.contact li::before{content:none}
.fcol.contact svg{position:absolute;left:0;top:4px}
.copyright{left:0;top:1162px;width:1038px;height:38px;background:var(--footer-deep);color:#ddd;font-size:11px;display:flex;align-items:center;justify-content:center}
</style>
</head>
<body>

<header>
  <div class="abs topbar">
    <div class="abs region">
      <svg width="28" height="16" viewBox="0 0 28 16" aria-hidden="true"><circle cx="9" cy="8" r="7" fill="none" stroke="#fff" stroke-width="1.4"/><path d="M2 8h14M9 1v14M4 4h10M4 12h10" stroke="#fff" stroke-width="1"/><path d="M21 7l3 3 3-3z" fill="#fff"/></svg>
      <span>Asia</span><span class="sep">|</span><span>Contact us</span>
    </div>
    <div class="abs pill phone">
      <svg width="11" height="11" viewBox="0 0 12 12" aria-hidden="true"><path d="M2 1h3l1 3-2 1a7 7 0 0 0 3 3l1-2 3 1v3c-6 0-9-3-9-9z" fill="#222"/></svg>
      0800.414.362
    </div>
    <div class="abs pill login">
      Login
      <svg width="13" height="12" viewBox="0 0 13 12" aria-hidden="true"><path d="M5 1h7v10H5" fill="none" stroke="#222" stroke-width="1.4"/><path d="M1 6h7M6 3l3 3-3 3" fill="none" stroke="#222" stroke-width="1.4"/></svg>
    </div>
  </div>

  <div class="abs header">
    <div class="abs logo"><span class="square"></span><span class="name">Torvel Capital</span></div>
    <ul class="abs nav">
      <li class="active">Home</li><li>About</li><li>Services</li><li>Current Engagements</li><li>Completed Transactions</li>
    </ul>
  </div>
</header>

<main>
  <section>
    <div class="abs worldmap" role="img" aria-label="Light grey world map with location pins"></div>
    <h1 class="abs hero-title">Torvel Capital, <b>LLC Investment</b> Banking<br>Mergers &amp; Acquisitions</h1>
    <p class="abs hero-text">Sed ut perspiciatis unde omnis iste natus error sit totam rem aperiam, eaque ipsa quae ab illo inventore veritatis et quasi architecto beatae vitae dicta sunt explicabo, Nemo enim ipsam voluptatem quia voluptas sit aspernatur aut odit aut fugit,</p>
    <div class="abs btn">Read More</div>
  </section>

  <section class="abs band"></section>
  <div class="abs service" style="left:95px">
    <h2>Buy-SideAcquisitions</h2>
    <ul><li>Lorem ipsum dolor sit amet, consectetur</li><li>adipisicing elit, sed do eiusmod tempor</li><li>incididunt ut labore et dolore magna aliqua.</li><li>Ut enim ad minim veniam</li><li class="more">Veiw all</li></ul>
  </div>
  <div class="abs divider" style="left:367px"></div>
  <div class="abs service" style="left:400px">
    <h2>Recapitalizations</h2>
    <ul><li>Lorem ipsum dolor sit amet, consectetur</li><li>adipisicing elit, sed do eiusmod tempor</li><li>incididunt ut labore et dolore magna aliqua.</li><li>Ut enim ad minim veniam</li><li class="more">Veiw all</li></ul>
  </div>
  <div class="abs divider" style="left:674px"></div>
  <div class="abs service" style="left:707px">
    <h2>Sell-SideTransactions</h2>
    <ul><li>Lorem ipsum dolor sit amet, consectetur</li><li>adipisicing elit, sed do eiusmod tempor</li><li>incididunt ut labore et dolore magna aliqua.</li><li>Ut enim ad minim veniam</li><li class="more">Veiw all</li></ul>
  </div>

  <section class="abs position">
    <h2>Positioning statement <small>Global, Professional, Trusted</small></h2>
    <p class="intro">Lorem ipsum dolor sit amet, consectetur adipiscing elit. Sed sagittis consectetur nunc in blandit. Donec aliquam, lacus vel semper congue, sem tellus tincidunt turpis, a vehicula leo</p>
    <p class="point"><a>Lorem ipsum dolor sit amet</a> - Consectetur adipiscing elit. Sed sagittis consectetur nunc in blandit. Donec aliquam, lacus vel semper congue, sem tellus tincidunt</p>
    <p class="point"><a>Lorem ipsum dolor sit amet</a> - Consectetur adipiscing elit. Sed sagittis consectetur nunc in blandit. Donec aliquam, lacus vel semper congue, sem tellusenim.</p>
  </section>
  <div class="abs dotted"></div>
  <section class="abs location"><h2>Our Location</h2></section>
  <div class="abs mapframe"><div role="img" aria-label="Street map showing the office location"></div></div>
</main>

<footer>
  <div class="abs footer">
    <div class="abs fcol" style="left:95px"><h3>Site Linke</h3>
      <ul><li>Home</li><li>About</li><li>Services</li><li>Current Engagements</li><li>Completed Transactions</li></ul></div>
    <div class="abs fcol" style="left:289px"><h3>Company</h3>
      <ul><li>About Northlane</li><li>Careers</li><li>Referral Program</li></ul></div>
    <div class="abs fcol" style="left:473px"><h3>Resources</h3>
      <ul><li>Blog</li><li>Articles</li><li>Webinars</li><li>Events</li><li>Downloads</li></ul></div>
    <div class="abs fcol" style="left:645px"><h3>Features</h3>
      <ul><li>Documentation</li><li>Scheduling</li><li>Practice Management</li><li>Billing</li><li>Compliance</li></ul></div>
    <div class="abs fcol contact" style="left:819px"><h3>Contact us</h3>
      <ul>
        <li><svg width="11" height="10" viewBox="0 0 11 10" aria-hidden="true"><path d="M5.5 0L0 5h1.5v5h3V7h2v3h3V5H11z" fill="#c9c9c9"/></svg>Request A Free Demo<br>Contact</li>
        <li><svg width="8" height="11" viewBox="0 0 8 11" aria-hidden="true"><rect x="1" y="0" width="6" height="11" rx="1" fill="none" stroke="#c9c9c9" stroke-width="1.2"/></svg>Phone: 866-470-3915</li>
        <li><svg width="11" height="11" viewBox="0 0 11 11" aria-hidden="true"><rect x="0" y="3" width="11" height="8" fill="#c9c9c9"/><rect x="3" y="0" width="6" height="4" fill="none" stroke="#c9c9c9"/></svg>Fax: 866-470-3988</li>
      </ul></div>
  </div>
  <div class="abs copyright">© Copyright 2014. All rights reseverd.</div>
</footer>

</body>
</html>
```